Wordpress Theme for Medical Clinics

** Please view updated Sitemap2.pdf doc to clarify some confusion ***

This is a multiuser WordPress subscription site for medical clinics. Please see attachment for sitemap. Please do not include extra content like social media icons, search bars, or images. If you have questions, please ask for clarification.
The site contains the following pages and sub-pages:

1. Home
2. Our Clinic
2a. Our Clinic > Mission
2b. Our Clinic > Services
2c. Our Clinic > Clinic Policies
2d. Our Clinic > Schedules
3. Our Staff
3a. Our Staff > [Staff member page]
4. Resources
4a. Resources > Patient Health (index)
4b. Resources > Patient Health (index) > [post]
4c. Resources > Links
4d. Resources > Forms
5. Alerts
5a. Alerts > [Alert Page]
6. Contact Us

Includes the Following Pages, Subpages, and Content
1. Home
a. About Us
b. Our Staff
c. Bulletins
d. Accepting New Patients (shown as an alert widget)
e. Links
i. Physician Toolbox
ii. Book an Appointment
f. Clinic Policies
i. Show first 3 policies (e.g. Late Arrivals, Missed Appointments, Fees)
ii. Link to Clinic Policies page
g. Primary widget (displayed on all pages)
i. Hours of operation
ii. Contact Info
1. Tel
2. Fax
3. Email
4. Address
5. Get directions (link to Route Finder)
2. Our Clinic
a. Main Page
i. Clinic Name
ii. Overview
iii. Languages Spoken
iv. Secondary Navigation
1. Mission
2. Services
3. Clinic Policies
4. Schedules (see attachment)
b. Our Clinic > Mission
c. Our Clinic > Services
i. For each service include service TITLE and DESCRIPTION
d. Our Clinic > Clinic Policies
i. For each policy include policy TITLE and DESCRIPTION
ii. Include the following policies in mockup
1. Late arrivals
2. Missed appointments
3. Fees for missed appointments
4. Referrals and follow-ups
5. Services not covered by RDA
6. Information for LTF patients
7. Medical Legal Reports
e. Our Clinic > Schedules
3. Our Staff
a. Main Page
i. Display a list of staff members. Include NAME and DESIGNATION
b. Our Staff > [Staff Name]
i. Include NAME, PICTURE, DESIGNATION, and BIO
4. Resources
a. Resources > Patient Health
i. Main Page
1. Posts (ordered by date)
a. Title
b. Summary
2. Side Navigation
a. Post Categories
ii. Patient Health > [post title]
1. Title
2. Post Category
3. Date
4. Author
5. Summary
6. Body
b. Resources > Links
1. Secondary Navigation - Categories
a. Sample Categories:
i. Local Services
ii. RDA and Drug Coverage
iii. Mental Health Resources
2. Category page
a. Include the following links in the 'Local Services' category
i. Hypertension clinics
ii. Home Care services
iii. Vaccine Clinics
c. Resources > Forms
i. Display a table with form TITLE and CATEGORY
ii. Side Navigation
1. Form Categories
a. Use the following sample Categories
i. Referrals
ii. Insurance
iii. Intake
iv. Discharge
v. Waivers
5. Alerts
a. Main page
i. List of all Alert posts
1. Include post TITLE as a link to the post
ii. Side Navigation
1. Alerts Archive
a. shown as Month + Number of posts
iii. Alerts > [Alert page]
1. Include TITLE, DATE, AUTHOR, BODY
6. Contact Us
a. Map
b. Hours of operation
c. Address
d. Phone number
e. Fax number
e. Fax number
f. Map
g. Email

Design notes:
- fixed width
- responsive (need designs for mobile, tablet, and desktop)
- simple, dark font, white background
- use Font Awesome icons where needed
- user adds own logo

Target Market(s)

Medical Clinics

Industry/Entity Type

Medical

Number of Pages Required

5+ page

Font styles to use
Serif
Sans Serif

Requirements
Must have
• Please keep designs very simple.
• Examples:
• https://www.quolbin.com/install
• http://www.ventrohax.com/company/about-us
• http://brindlequota.org/
• http://www.trosk.com/
Should not have
• Minimal or no use of shadows and gradients

```html
<!DOCTYPE html>
<html lang="en">
<head>
<meta charset="utf-8">
<title>Clinic Name — Home</title>
<link href="https://fonts.googleapis.com/css2?family=Open+Sans:ital,wght@0,400;0,600;0,700;0,800;1,400&display=swap" rel="stylesheet">
<style>
  :root{
    --accent:#2aa6de;
    --accent-soft:#bfe5f6;
    --ink:#222;
    --text:#555;
    --muted:#888;
    --band:#f5f5f5;
    --line:#e6e6e6;
    --footer:#2f2f2f;
    --white:#fff;
  }
  *{box-sizing:border-box;margin:0;padding:0}
  html,body{width:1200px;height:3618px;overflow:hidden}
  body{font-family:"Open Sans",Arial,sans-serif;color:var(--text);background:var(--white);font-size:13px;line-height:1.65}
  a{color:var(--accent);text-decoration:none}
  .container{width:1050px;margin:0 auto;position:relative}

  /* hero */
  .hero{height:654px;position:relative;overflow:hidden}
  .hero-photo{position:absolute;inset:0;background:linear-gradient(180deg,#eef1f3 0%,#f7f8f9 35%,#dfe9ef 70%,#c9dde8 100%)}
  .hero-title{position:absolute;left:0;right:0;top:322px;text-align:center;color:#161616;text-transform:uppercase;line-height:1.25}
  .hero-title strong{display:block;font-weight:800;font-size:34px;letter-spacing:.5px}
  .hero-title span{display:block;font-weight:400;font-size:31px}

  /* nav */
  .site-header{height:60px;border-bottom:1px solid var(--line);background:var(--white)}
  .site-header .container{display:flex;align-items:center;justify-content:space-between;height:60px;width:1056px}
  .brand{font-size:22px;font-weight:700;color:var(--ink);letter-spacing:.5px;text-transform:uppercase}
  .main-nav{display:flex;height:60px;margin-right:-18px}
  .main-nav a{display:flex;align-items:center;padding:0 26px;font-size:11px;font-weight:600;color:var(--ink);text-transform:uppercase;letter-spacing:.4px;border-top:3px solid transparent;border-bottom:3px solid transparent}
  .main-nav a.active{color:var(--accent);border-bottom-color:var(--accent)}

  /* about */
  .about{height:456px;padding-top:66px}
  .about .container{display:flex;gap:30px}
  .about-photo{width:510px;height:330px;background:linear-gradient(135deg,#dfe6ea,#b9c6cd 55%,#8fa2ad)}
  .about-body{flex:1}
  .section-title{font-size:23px;font-weight:700;color:var(--ink);text-transform:uppercase;display:flex;align-items:center;gap:10px;line-height:1.2}
  .about-body .section-title{margin:10px 0 20px}
  .about-body p{font-size:13px;margin-bottom:18px;line-height:1.8}

  /* info widgets */
  .info{background:var(--band);height:525px;padding-top:66px}
  .info .container{display:flex;gap:30px}
  .widget{background:var(--white);border:5px solid var(--accent-soft);padding:24px 26px;height:393px;position:relative;flex:1}
  .widget h3{font-size:16px;font-weight:600;color:var(--ink);text-transform:uppercase;display:flex;align-items:center;gap:8px;margin-bottom:20px}
  .widget h3 svg{fill:var(--accent)}
  .btn{display:inline-block;border:3px solid var(--accent);color:var(--accent);font-size:12px;font-weight:600;text-transform:uppercase;padding:9px 16px;background:var(--white);letter-spacing:.3px}
  .widget .btn{position:absolute;left:26px;bottom:30px}
  .data-table{width:100%;border-collapse:collapse;font-size:12px}
  .data-table td{padding:9px 0;border-bottom:1px solid #eee;vertical-align:top}
  .data-table td:first-child{font-weight:700;color:var(--ink);text-transform:uppercase;font-size:11px;width:48%}
  .data-table tr:last-child td{border-bottom:0}
  .hours td:last-child{color:var(--accent)}

  /* staff */
  .staff{height:630px;padding-top:66px}
  .staff .section-title{justify-content:center;margin-bottom:24px}
  .staff-grid{display:flex;justify-content:space-between}
  .staff-col{width:250px}
  .staff-card{margin-bottom:32px}
  .staff-card h4{font-size:14px;font-weight:700;color:var(--accent);text-transform:uppercase}
  .staff-card .role{font-size:15px;color:var(--ink);margin-bottom:6px}
  .staff-card p{font-size:12px;line-height:1.6}
  .staff-card em{color:var(--muted)}
  .staff-center{width:528px;text-align:center}
  .staff-photo{height:390px;background:radial-gradient(ellipse at 50% 55%,#e4ecf0 0%,#f4f7f8 55%,#fff 80%)}
  .staff-center .btn{margin-top:24px}

  /* alerts + policies */
  .notices{background:var(--band);height:525px;padding-top:75px}
  .notices .container{display:flex;gap:36px}
  .notices .widget{height:384px}
  .alert-item{display:flex;gap:22px;margin-bottom:26px}
  .date-badge{flex:none}
  .alert-item h5{font-size:12px;font-weight:700;color:var(--ink);text-transform:uppercase;margin-bottom:6px;line-height:1.5}
  .alert-item p{font-size:12px;line-height:1.6}
  .policy-list{list-style:none;margin-top:6px}
  .policy-list li{font-size:11px;font-weight:700;color:var(--ink);text-transform:uppercase;padding-left:14px;position:relative;margin-bottom:10px}
  .policy-list li::before{content:"";position:absolute;left:0;top:7px;width:4px;height:4px;background:var(--ink);border-radius:50%}

  /* location */
  .location{height:690px;padding-top:70px}
  .location .section-title{justify-content:center;margin-bottom:30px}
  .map{width:921px;height:501px;margin:0 auto;background:linear-gradient(135deg,#efe8d8,#e6dcc3 40%,#d9e6c8 70%,#c7dcea)}

  /* footer */
  .site-footer{background:var(--footer);height:78px;color:#ccc;font-size:11px}
  .site-footer .container{display:flex;justify-content:space-between;padding-top:22px;width:1056px}
  .site-footer a{color:#ccc}
</style>
</head>
<body>

<section class="hero">
  <div class="hero-photo" role="img" aria-label="Photo of four smiling doctors in white coats"></div>
  <h1 class="hero-title"><strong>Free online lorem ipsum dummy text</strong><span>generator with great features</span></h1>
</section>

<header class="site-header">
  <div class="container">
    <div class="brand">Clinic Name</div>
    <nav class="main-nav">
      <a class="active" href="#">Home</a>
      <a href="#">Our Clinic</a>
      <a href="#">Our Staff</a>
      <a href="#">Resources</a>
      <a href="#">Alerts</a>
      <a href="#">Contact Us</a>
    </nav>
  </div>
</header>

<section class="about">
  <div class="container">
    <div class="about-photo" role="img" aria-label="Photo of a bright clinic hallway"></div>
    <div class="about-body">
      <h2 class="section-title">
        <svg width="20" height="22" viewBox="0 0 20 22"><rect x="2" y="3" width="16" height="18" rx="1" fill="none" stroke="#222" stroke-width="2"/><rect x="7" y="1" width="6" height="4" fill="#222"/><path d="M10 9v7M6.5 12.5h7" stroke="#222" stroke-width="2"/></svg>
        About Our Clinic
      </h2>
      <p>Lorem Ipsum is simply dummy text of the printing and typesetting industry. Lorem Ipsum has been the industry's standard dummy text ever since the 1500s, when an unknown printer took a galley of type and scrambled it to make a type specimen book. It has survived not only five centuries, but also the leap into electronic typesettdesktop publishing software like Ferrow Layout including versions of Lorem Ipsum.</p>
      <p>Lorem Ipsum is simply dummy text of the printing and typesetting industry. It has survived not only five centuries, but also the leap into electronic desktop publishing software like Ferrow Layout including versions of Lorem Ipsum.</p>
    </div>
  </div>
</section>

<section class="info">
  <div class="container">
    <div class="widget">
      <h3><svg width="14" height="16" viewBox="0 0 14 16"><circle cx="7" cy="4" r="4"/><path d="M0 16c0-5 3-7 7-7s7 2 7 7z"/></svg>New Patients</h3>
      <p style="font-size:12px">Accepting new patients</p>
      <a class="btn" href="#">Contact Us</a>
    </div>
    <div class="widget">
      <h3><svg width="16" height="16" viewBox="0 0 16 16"><circle cx="8" cy="8" r="7" fill="none" stroke="#2aa6de" stroke-width="2"/><path d="M8 4v4.5l3 2" stroke="#2aa6de" stroke-width="2" fill="none"/></svg>Hours of Operation</h3>
      <table class="data-table hours">
        <tr><td>Monday</td><td>8:00am - 6:00pm</td></tr>
        <tr><td>Tuesday</td><td>8:00am - 6:00pm</td></tr>
        <tr><td>Wednesday</td><td>8:00am - 6:00pm</td></tr>
        <tr><td>Thursday</td><td>8:00am - 6:00pm</td></tr>
        <tr><td>Friday</td><td>8:00am - 6:00pm</td></tr>
        <tr><td>Saturday</td><td>9:00am - 4:00pm</td></tr>
        <tr><td>Sunday</td><td>9:00am - 4:00pm</td></tr>
      </table>
    </div>
    <div class="widget">
      <h3><svg width="16" height="12" viewBox="0 0 16 12"><rect width="16" height="12" rx="1"/><path d="M1 1l7 6 7-6" stroke="#fff" stroke-width="1.5" fill="none"/></svg>Contact Info</h3>
      <table class="data-table">
        <tr><td>Telephone</td><td>250 555 0142</td></tr>
        <tr><td>Fax</td><td>250 555 0143</td></tr>
        <tr><td>Email</td><td><a href="#">hello@clinicname.ca</a></td></tr>
        <tr><td>Address</td><td>47 Alder Lane,<br>Brookfield, B.C.,<br>Canada V0X2K4</td></tr>
        <tr><td>Directions</td><td><a href="#">Route Finder</a></td></tr>
      </table>
    </div>
  </div>
</section>

<section class="staff">
  <div class="container">
    <h2 class="section-title">
      <svg width="24" height="18" viewBox="0 0 24 18" fill="#222"><circle cx="12" cy="5" r="4"/><path d="M5 18c0-5 3-7 7-7s7 2 7 7z"/><circle cx="4.5" cy="6" r="3"/><circle cx="19.5" cy="6" r="3"/><path d="M0 15c0-3 2-5 4.5-5 1 0 2 .3 2.6.8C5.5 12 4.6 13.5 4.3 15z M24 15c0-3-2-5-4.5-5-1 0-2 .3-2.6.8 1.6 1.2 2.5 2.7 2.8 4.2z"/></svg>
      Our Staff
    </h2>
    <div class="staff-grid">
      <div class="staff-col">
        <div class="staff-card"><h4>Dr. John Smith, MD</h4><div class="role">Physician</div><p>In publishing and graphic design, lorem ipsum graphic elements of a document or visual presentation. <em>[Read more]</em></p></div>
        <div class="staff-card"><h4>Dr. John Smith, MD</h4><div class="role">Physician</div><p>In publishing and graphic design, lorem ipsum graphic elements of a document or visual presentation. <em>[Read more]</em></p></div>
        <div class="staff-card"><h4>Dr. John Smith, MD</h4><div class="role">Physician</div><p>In publishing and graphic design, lorem ipsum graphic elements of a document or visual presentation. <em>[Read more]</em></p></div>
      </div>
      <div class="staff-center">
        <div class="staff-photo" role="img" aria-label="Photo of two physicians in white coats"></div>
        <a class="btn" href="#">View All Staff</a>
      </div>
      <div class="staff-col">
        <div class="staff-card"><h4>Dr. John Smith, MD</h4><div class="role">Physician</div><p>In publishing and graphic design, lorem ipsum graphic elements of a document or visual presentation. <em>[Read more]</em></p></div>
        <div class="staff-card"><h4>Dr. John Smith, MD</h4><div class="role">Physician</div><p>In publishing and graphic design, lorem ipsum graphic elements of a document or visual presentation. <em>[Read more]</em></p></div>
        <div class="staff-card"><h4>Dr. John Smith, MD</h4><div class="role">Physician</div><p>In publishing and graphic design, lorem ipsum graphic elements of a document or visual presentation. <em>[Read more]</em></p></div>
      </div>
    </div>
  </div>
</section>

<section class="notices">
  <div class="container">
    <div class="widget">
      <h3><svg width="14" height="16" viewBox="0 0 14 16"><path d="M7 0c3 0 5 2 5 5v5l2 3H0l2-3V5c0-3 2-5 5-5zM5 14h4c0 1-1 2-2 2s-2-1-2-2z"/></svg>Alerts</h3>
      <div class="alert-item">
        <svg class="date-badge" width="62" height="62" viewBox="0 0 62 62"><rect x="3" y="8" width="56" height="51" rx="3" fill="none" stroke="#2aa6de" stroke-width="4"/><rect x="3" y="8" width="56" height="12" fill="#2aa6de"/><rect x="15" y="2" width="5" height="12" fill="#2aa6de"/><rect x="42" y="2" width="5" height="12" fill="#2aa6de"/><text x="31" y="50" text-anchor="middle" font-family="Open Sans, sans-serif" font-size="25" font-weight="700" fill="#2aa6de">23</text></svg>
        <div><h5>A handy lorem ipsum generator for all layout needs</h5><p>In publishing and graphic design, lorem as ipsum is filler text commonly used to demo instate the graphic elements of a aliquam erat volutpat. Ut wisi enim...</p></div>
      </div>
      <div class="alert-item">
        <svg class="date-badge" width="62" height="62" viewBox="0 0 62 62"><rect x="3" y="8" width="56" height="51" rx="3" fill="none" stroke="#2aa6de" stroke-width="4"/><rect x="3" y="8" width="56" height="12" fill="#2aa6de"/><rect x="15" y="2" width="5" height="12" fill="#2aa6de"/><rect x="42" y="2" width="5" height="12" fill="#2aa6de"/><text x="31" y="50" text-anchor="middle" font-family="Open Sans, sans-serif" font-size="25" font-weight="700" fill="#2aa6de">23</text></svg>
        <div><h5>A handy lorem ipsum generator for all layout needs</h5><p>In publishing and graphic design, lorem as ipsum is filler text commonly used to demo instate the graphic elements of a aliquam erat volutpat. Ut wisi enim...</p></div>
      </div>
    </div>
    <div class="widget">
      <h3><svg width="13" height="16" viewBox="0 0 13 16"><path d="M0 0h9l4 4v12H0z"/><path d="M3 7h7M3 10h7M3 13h5" stroke="#fff" stroke-width="1.2"/></svg>Clinic Policies</h3>
      <ul class="policy-list">
        <li>Late Arrivals</li>
        <li>Missed Appointments</li>
        <li>Fees</li>
      </ul>
      <a class="btn" href="#">View All Clinic Policies</a>
    </div>
  </div>
</section>

<section class="location">
  <div class="container">
    <h2 class="section-title">
      <svg width="16" height="22" viewBox="0 0 16 22"><path d="M8 0C3.6 0 0 3.5 0 8c0 6 8 14 8 14s8-8 8-14c0-4.5-3.6-8-8-8z" fill="#222"/><circle cx="8" cy="8" r="3" fill="#fff"/></svg>
      Our Location
    </h2>
    <div class="map" role="img" aria-label="Street map showing the clinic location"></div>
  </div>
</section>

<footer class="site-footer">
  <div class="container">
    <span>©2015 Clinic Name. All Rights Reserved</span>
    <span><a href="#">Terms &amp; Privacy Policy</a> | <a href="#">Sitemap</a></span>
  </div>
</footer>

</body>
</html>
```